3 in 1 website - Property Lens Works + Keepsake Harbor LLC + Marla's Game Shots

Help me simplify and organize my business life. I am a sports photographer (action, individual and teams), real estate photographer (stills and drones) and I transfer videos and photos to jump drives, along with photo restoration, etc. Currently, I have a functioning website for the transfer/restoration business at KeepsakeHarborLLC.example which was recently created and I like it. I have received several really good ideas for the Real Estate Photography portion! I don't have anything started for the Sports Pics. My vision possibly includes a main/home page giving people the option to choose real estate, sports or transfer/restoration. I just want them combined into one site....somehow to better organize my businesses and give me ONE place to keep to updated and check for communication. I just updated the brief again and added logo files for my "parent" company called "Keepsake Harbor". I prefer this logo at the top of the main/home page, please. I previously uploaded the logo for Property Lens Works which would be used with the real estate portion of my business. At this point, I don't have a logo for the sports photography portion.

Target Market(s)

Real Estate Agents and Brokers; Sports team, parents and boosters; Community members typically 40+ years old

Industry/Entity Type

Real Estate Photography; Local sports teams; Community members 40+ years old

Coding

Coded - Design and coding required

Number of Pages Required

3 page

Requirements
Must have
• At least one page for each area: real estate, sports, digital transfers. The real estate will need to connect to an account I have with QLN for checkout options. The sports page(s) will need to connect to a 3rd party service, also. The digital transfers, photo restorations, etc. would just need a way for them to request service.
Nice to have
• I currently have a website at KeepsakeHarborLLC.example for the digital transfer/photo restoration part of my business. I like this website but want it integrated with one main site for all 3 businesses.

```html
<!DOCTYPE html>
<html lang="en">
<head>
<meta charset="utf-8">
<title>Wren Calloway Real Estate Photography</title>
<link href="https://fonts.googleapis.com/css2?family=Michroma&family=Roboto:wght@400;500;700&display=swap" rel="stylesheet">
<style>
:root{
  --red:#e41d20;
  --blue:#0a6bc4;
  --blue-deep:#0758a8;
  --ink:#1d1d1d;
  --text:#666666;
  --muted:#8a8a8a;
  --white:#ffffff;
  --field:#ffffff;
  --footer:#111214;
}
*{box-sizing:border-box;margin:0;padding:0}
html,body{width:1200px;height:4125px;overflow:hidden}
body{position:relative;background:var(--white);font-family:"Roboto",Arial,sans-serif;color:var(--text)}
.abs{position:absolute}
.heading{font-family:"Michroma","Arial",sans-serif;font-weight:400;color:var(--ink);letter-spacing:-1px;text-transform:uppercase}
.copy{font-size:14.5px;line-height:26.6px;color:var(--text)}
.btn{position:absolute;display:flex;align-items:center;justify-content:center;background:var(--red);color:var(--white);font-weight:700;font-size:16px;clip-path:polygon(7% 0,100% 0,93% 100%,0 100%);text-decoration:none}

/* header */
.top-rule{left:0;top:0;width:1200px;height:4px;background:var(--red)}
.header{left:0;top:4px;width:1200px;height:108px;background:var(--white)}
.contact-mini{top:22px;display:flex;align-items:center;gap:14px;font-size:14px;color:var(--muted)}
.contact-mini .ico{width:26px;height:26px;border-radius:50%;background:var(--blue);display:flex;align-items:center;justify-content:center}
.nav{top:67px;display:flex;gap:42px;font-size:14.5px;font-weight:500;color:#333}
.nav-right{gap:27px}
.brand-plate{left:436px;top:4px;width:317px;height:156px;background:var(--white);clip-path:polygon(0 0,100% 0,92% 100%,8% 100%);z-index:3;display:flex;align-items:center;justify-content:center;gap:10px;padding-top:18px}
.brand-plate .mark{width:14px;height:14px;background:var(--red)}
.brand-name{font-family:"Roboto",Arial,sans-serif;font-weight:700;font-size:22px;color:var(--red);text-transform:uppercase}

/* hero */
.hero{left:0;top:112px;width:1200px;height:745px;background:
  radial-gradient(ellipse 260px 220px at 600px 250px,rgba(40,120,200,.35),transparent 70%),
  radial-gradient(ellipse 340px 260px at 140px 470px,rgba(18,16,14,.85),transparent 75%),
  radial-gradient(ellipse 300px 320px at 1060px 250px,rgba(92,72,52,.7),transparent 70%),
  radial-gradient(ellipse 420px 200px at 600px 120px,rgba(120,100,80,.45),transparent 70%),
  linear-gradient(180deg,#3a342d 0%,#443a30 35%,#2e2822 70%,#1f1b18 100%)}
.hero-title{left:0;top:530px;width:1200px;text-align:center;font-size:39px;line-height:45px;color:var(--white);letter-spacing:-1px}

/* about */
.about-card{left:111px;top:766px;width:977px;height:541px;background:var(--white);border-top:5px solid var(--blue);box-shadow:0 4px 14px rgba(0,0,0,.18)}
.about-photo{left:634px;top:796px;width:439px;height:490px;border-radius:6px;background:
  radial-gradient(ellipse 150px 150px at 230px 130px,rgba(176,126,78,.95),transparent 70%),
  radial-gradient(ellipse 170px 150px at 230px 400px,rgba(62,92,140,.95),transparent 75%),
  radial-gradient(ellipse 90px 60px at 240px 440px,rgba(30,30,32,.9),transparent 70%),
  linear-gradient(100deg,#c9bba7 0%,#d9d3c8 30%,#b9a38a 55%,#a9b4c4 80%,#8c9db3 100%)}
.bullets{left:205px;top:1018px;list-style:none;font-size:14.5px;color:var(--text)}
.bullets li{height:29px;display:flex;align-items:center;gap:14px}
.bullets li::before{content:"";width:9px;height:9px;border-radius:50%;border:2px solid #777;box-shadow:inset 0 0 0 2px #fff;background:#777}
.signature{left:181px;top:1122px;font-size:17px;font-weight:500;color:var(--ink)}
.role{left:181px;top:1151px;font-size:13.5px;color:var(--text)}

/* real estate */
.center-copy{text-align:center}
.estate-photo{left:0;top:1623px;width:1200px;height:408px;background:
  radial-gradient(ellipse 140px 260px at 40px 230px,rgba(92,118,64,.9),transparent 75%),
  radial-gradient(ellipse 150px 280px at 1170px 200px,rgba(84,110,56,.9),transparent 75%),
  radial-gradient(ellipse 220px 150px at 380px 250px,rgba(222,216,200,.95),transparent 72%),
  radial-gradient(ellipse 200px 120px at 780px 280px,rgba(214,208,192,.9),transparent 72%),
  linear-gradient(180deg,#ffffff 0%,#f2f4f5 25%,#d9dad3 60%,#9ea58b 85%,#4d6a2f 94%,#3f5a27 100%)}

/* sports */
.sports-band{left:0;top:2031px;width:1200px;height:503px;background:linear-gradient(180deg,var(--blue) 0%,var(--blue-deep) 100%)}
.sports-photo{left:607px;top:2081px;width:474px;height:575px;box-shadow:0 6px 16px rgba(0,0,0,.25);background:
  radial-gradient(ellipse 70px 90px at 240px 250px,rgba(255,244,210,1),transparent 75%),
  radial-gradient(ellipse 200px 220px at 240px 260px,rgba(40,58,44,.9),transparent 80%),
  radial-gradient(ellipse 260px 110px at 240px 520px,rgba(120,110,70,.8),transparent 75%),
  linear-gradient(180deg,#e8dfc8 0%,#d8c79a 30%,#7e7a55 62%,#4d5233 82%,#6a5e38 100%)}

/* digital */
.digital-photo{left:111px;top:2735px;width:488px;height:469px;box-shadow:0 4px 12px rgba(0,0,0,.2);background:
  radial-gradient(circle 110px at 300px 220px,rgba(140,150,158,.95),rgba(40,44,48,.9) 55%,transparent 75%),
  radial-gradient(ellipse 220px 180px at 190px 170px,rgba(26,28,32,.95),transparent 75%),
  radial-gradient(ellipse 260px 120px at 300px 410px,rgba(170,160,140,.8),transparent 75%),
  linear-gradient(150deg,#e8edf1 0%,#b7c0c8 40%,#8b949b 70%,#cfd3d4 100%)}

/* contact */
.info-item{left:122px;display:flex;gap:16px}
.info-ico{width:50px;height:50px;border-radius:50%;border:2px solid var(--red);display:flex;align-items:center;justify-content:center;flex:none}
.info-title{font-size:18px;color:var(--ink);margin-top:2px}
.info-text{font-size:14.5px;line-height:25.6px;color:var(--text)}
.field{left:445px;width:318px;height:51px;background:var(--field);box-shadow:0 2px 8px rgba(0,0,0,.12);font-size:14.5px;color:var(--muted);padding:16px 24px}
.message{left:783px;top:3361px;width:300px;height:258px}
.submit{left:445px;top:3568px;width:330px;height:51px;background:var(--blue);color:var(--white);font-weight:700;font-size:16px;display:flex;align-items:center;justify-content:center;clip-path:polygon(3% 0,100% 0,97% 100%,0 100%)}

/* footer */
.footer{left:0;top:3746px;width:1200px;height:379px;background:var(--footer)}
.footer-brand{left:0;top:3880px;width:1200px;display:flex;justify-content:center;align-items:center;gap:12px}
.footer-brand .mark{width:16px;height:16px;background:var(--red)}
.footer-brand .brand-name{font-size:32px}
.footer-nav{left:0;top:3978px;width:1200px;display:flex;justify-content:center;gap:28px;font-size:13.5px;font-weight:500;color:var(--white)}
.footer-nav .sep{color:#bbb}
.copyright{left:0;top:4024px;width:1200px;text-align:center;font-size:11.5px;color:#ddd}
.socials{left:0;top:4064px;width:1200px;display:flex;justify-content:center;gap:10px}
.socials span{width:22px;height:22px;border-radius:50%;background:var(--blue)}
</style>
</head>
<body>

<div class="abs top-rule"></div>

<header class="abs header">
  <div class="abs contact-mini" style="left:128px">
    <span class="ico"><svg width="13" height="13" viewBox="0 0 24 24"><path fill="#fff" d="M6.6 10.8a15.1 15.1 0 0 0 6.6 6.6l2.2-2.2c.3-.3.7-.4 1-.2 1.1.4 2.3.6 3.6.6.6 0 1 .4 1 1V20c0 .6-.4 1-1 1A17 17 0 0 1 3 4c0-.6.4-1 1-1h3.5c.6 0 1 .4 1 1 0 1.3.2 2.5.6 3.6.1.3 0 .7-.2 1z"/></svg></span>
    +1 555 0142-300
  </div>
  <div class="abs contact-mini" style="left:912px">
    <span class="ico"><svg width="14" height="14" viewBox="0 0 24 24"><rect x="3" y="6" width="18" height="12" rx="2" fill="none" stroke="#fff" stroke-width="2"/><path d="M3 7l9 6 9-6" fill="none" stroke="#fff" stroke-width="2"/></svg></span>
    info@wrencalloway.example
  </div>
  <nav class="abs nav" style="left:128px"><span>Home</span><span>About Us</span><span>Real Estate</span></nav>
  <nav class="abs nav nav-right" style="left:804px"><span>Sports</span><span>Digital Transfers</span><span>Contact</span></nav>
</header>

<div class="abs brand-plate"><span class="mark"></span><span class="brand-name">Wren Calloway</span></div>

<section class="abs hero" role="img" aria-label="Dimly lit living room interior photograph"></section>
<h1 class="abs heading hero-title">Wren Calloway Real Estate<br>Photography</h1>
<a class="btn" style="left:516px;top:647px;width:166px;height:42px">Get A Quote</a>

<section class="abs about-card"></section>
<h2 class="abs heading" style="left:181px;top:840px;font-size:34px">About Me</h2>
<p class="abs copy" style="left:181px;top:899px;width:410px">Contrary to popular belief, Lorem Ipsum is not simply random text. It has roots in a piece of classical Latin literature from 45 BC, making it over 2000 years old. Aldous Penwright, a Latin professor at Linford-Ashby College</p>
<ul class="abs bullets">
  <li>Lorem Ipsum is not simply random text</li>
  <li>Lorem Ipsum is not simply random text</li>
  <li>Lorem Ipsum is not simply random text</li>
</ul>
<div class="abs signature">Tessa Morrow</div>
<div class="abs role">( Position Name) &nbsp;&nbsp; Wren</div>
<a class="btn" style="left:181px;top:1197px;width:167px;height:41px">Read More</a>
<div class="abs about-photo" role="img" aria-label="Photographer holding a camera on a city street"></div>

<h2 class="abs heading center-copy" style="left:0;top:1395px;width:1200px;font-size:34px">Real Estate</h2>
<p class="abs copy center-copy" style="left:175px;top:1457px;width:850px">Contrary to popular belief, Lorem Ipsum is not simply random text. It has roots in a piece of classical Latin literature from 45 BC, making it over 2000 years old. Aldous Penwright, a Latin professor at Linford-Ashby College &nbsp;in Virginia, looked up one of the more obscure Latin words , consectetur, from a Lorem Ipsum passage, and going through the cites of the word in classical literature, discovered the undoubtable sourceLorem Ipsum comes from sections</p>
<div class="abs estate-photo" role="img" aria-label="Modern white apartment buildings among trees and lawn"></div>
<p class="abs copy center-copy" style="left:0;top:1591px;width:1200px">Bonorum et Malorum" (The Extremes of Good and Evil) by Orelius, written in 45 BC.<br>This book is a treatise on the theory of ethics, very popular during the Renaissance. The first line of Lorem Ipsum, "Lorem</p>
<a class="btn" style="left:516px;top:1676px;width:166px;height:41px">Read More</a>

<section class="abs sports-band"></section>
<h2 class="abs heading" style="left:111px;top:2107px;font-size:34px;color:var(--white)">Sports</h2>
<p class="abs copy" style="left:111px;top:2169px;width:420px;color:var(--white)">Contrary to popular belief, Lorem Ipsum is not simply random text. It has roots in a piece of classical Latin literature from 45 BC, making it over 2000 years old. Aldous Penwright, a Latin professor at Linford-Ashby College in Virginia, looked up one of the more obscure Latin words</p>
<p class="abs copy" style="left:111px;top:2329px;width:400px;color:var(--white)">consectetur, from a Lorem Ipsum passage, and going through the cites of the</p>
<a class="btn" style="left:111px;top:2406px;width:167px;height:42px">Read More</a>
<div class="abs sports-photo" role="img" aria-label="Soccer team huddling on a field at sunset"></div>

<div class="abs digital-photo" role="img" aria-label="Vintage folding camera resting on old photographs"></div>
<h2 class="abs heading" style="left:649px;top:2780px;font-size:34px">Digital Transfers</h2>
<p class="abs copy" style="left:649px;top:2845px;width:420px">Contrary to popular belief, Lorem Ipsum is not simply random text. It has roots in a piece of classical Latin literature from 45 BC, making it over 2000 years old. Aldous Penwright, a Latin professor at Linford-Ashby College in Virginia, looked up one of the more obscure Latin words</p>
<p class="abs copy" style="left:649px;top:3004px;width:400px">, consectetur, from a Lorem Ipsum passage, and going through the cites of the word in classical literature, discovered the undoubtable source.</p>
<a class="btn" style="left:649px;top:3108px;width:167px;height:42px">Read More</a>

<h2 class="abs heading center-copy" style="left:0;top:3284px;width:1200px;font-size:34px">Contact Us</h2>

<div class="abs info-item" style="top:3362px">
  <span class="info-ico"><svg width="16" height="18" viewBox="0 0 24 24"><path fill="#e41d20" d="M12 2a7 7 0 0 0-7 7c0 5 7 13 7 13s7-8 7-13a7 7 0 0 0-7-7zm0 9.5A2.5 2.5 0 1 1 12 6.5a2.5 2.5 0 0 1 0 5z"/></svg></span>
  <div><div class="info-title">Location</div><div class="info-text">14Y, Wren Calloway Real Estate<br>Photography, Lorem ipsum</div></div>
</div>
<div class="abs info-item" style="top:3467px">
  <span class="info-ico"><svg width="16" height="16" viewBox="0 0 24 24"><path fill="#e41d20" d="M6.6 10.8a15.1 15.1 0 0 0 6.6 6.6l2.2-2.2c.3-.3.7-.4 1-.2 1.1.4 2.3.6 3.6.6.6 0 1 .4 1 1V20c0 .6-.4 1-1 1A17 17 0 0 1 3 4c0-.6.4-1 1-1h3.5c.6 0 1 .4 1 1 0 1.3.2 2.5.6 3.6.1.3 0 .7-.2 1z"/></svg></span>
  <div><div class="info-title">Phone</div><div class="info-text">+1 555 014 2300</div></div>
</div>
<div class="abs info-item" style="top:3562px">
  <span class="info-ico"><svg width="16" height="14" viewBox="0 0 24 20"><rect x="2" y="3" width="20" height="14" rx="2" fill="#e41d20"/><path d="M3 4l9 6 9-6" fill="none" stroke="#fff" stroke-width="2"/></svg></span>
  <div><div class="info-title">Email</div><div class="info-text">&nbsp;info@wrencalloway.example</div></div>
</div>

<div class="abs field" style="top:3361px">Name</div>
<div class="abs field" style="top:3430px">Phone</div>
<div class="abs field" style="top:3497px">Email</div>
<div class="abs submit">Submit</div>
<div class="abs field message">Type your message</div>

<footer class="abs footer"></footer>
<div class="abs footer-brand"><span class="mark"></span><span class="brand-name">Wren Calloway</span></div>
<nav class="abs footer-nav">
  <span>Home</span><span class="sep">|</span><span>About Us</span><span class="sep">|</span><span>Real Estate</span><span class="sep">|</span><span>Sports</span><span class="sep">|</span><span>Digital Transfers</span><span class="sep">|</span><span>Contact Us</span>
</nav>
<div class="abs copyright">© Copyrights 2023 Wren Calloway Real Estate Photography | All Rights Reserved</div>
<div class="abs socials"><span></span><span></span><span></span></div>

</body>
</html>
```